New Business Card Design for Manufacturing

We are an engineering/manufacturing company that offers Advanced machining/assembly/engineering services, as well as innovative products for the heavy duty engine cooling markets.

We are looking to get a new business card designed that is clean and modern looking, but still fits the wide range of technical/skilled work we do.

- We hope to use this design as the base for other design work in new Presentations, web, and print work.

Industry/Entity Type

Engineering

Contact Information for Business Card

Our preferred color of blue is (RGB) 22/71/159 but can vary slightly from that color. Our content will be our Logo and full company name (Vantrell Forge Works, Inc.), company address, name, job title, phone number with extension, cell number, fax number, website, and email address on the cards.
We'd like the full company name next to the logo, but we are open to other interpretations of that layout.
Preferably, we would like the back side to be clean with just our logo, and the front to contain all of the contact information.

Colors
2f74b4
0355a3
85abd2

Requirements
Must have
• - Logo, company name, needed content - We are open to interpretation beyond that.
• - Standard size business card.
• - Horizontal orientation.
• - Enough space for lengthy names / job titles (for example, a job title could read "Directory of Human Resources" or "V.P. of Governmental Affairs"). We need this to look clean, whether the title be short (CEO) or long (as described above).

```html
<!DOCTYPE html>
<html lang="en">
<head>
<meta charset="utf-8">
<title>Vantrell Forge Works – Business Card</title>
<link href="https://fonts.googleapis.com/css2?family=Open+Sans:wght@400;600;700&display=swap" rel="stylesheet">
<style>
  :root {
    --scene-bg: #3a3a3c;
    --card-black: #1d1d1f;
    --logo-gloss: #2c2c2f;
    --brand-blue: #0355a3;
    --brand-blue-light: #2f74b4;
    --brand-blue-pale: #85abd2;
    --text-white: #f2f2f2;
    --strip-grey: #8e959c;
  }
  * { margin: 0; padding: 0; box-sizing: border-box; }
  html, body { width: 799px; height: 1200px; overflow: hidden; }
  body {
    background: var(--scene-bg);
    font-family: "Open Sans", Arial, sans-serif;
    position: relative;
  }
  .card {
    position: absolute;
    left: 70px;
    width: 660px;
    height: 377px;
    background: var(--card-black);
    border-radius: 4px;
    overflow: hidden;
    box-shadow: 0 18px 40px rgba(0,0,0,.45);
  }
  .card--back { top: 150px; }
  .card--front { top: 680px; }

  .back-wordmark {
    position: absolute;
    left: 0; right: 0; top: 150px;
    text-align: center;
    font-size: 64px;
    font-weight: 700;
    letter-spacing: 2px;
    color: var(--logo-gloss);
  }

  .front-wordmark {
    position: absolute;
    right: 44px; top: 62px;
    font-size: 52px;
    font-weight: 700;
    color: var(--brand-blue-light);
    letter-spacing: 1px;
  }

  .person { position: absolute; left: 40px; top: 52px; }
  .person__name { font-size: 27px; font-weight: 600; color: var(--brand-blue-light); line-height: 1.1; }
  .person__title { font-size: 14px; color: var(--text-white); margin-top: 4px; }

  .contact-list { position: absolute; left: 40px; top: 138px; list-style: none; }
  .contact-list li {
    display: flex; align-items: center; gap: 10px;
    font-size: 15px; color: var(--text-white); line-height: 25px;
  }
  .contact-list svg { width: 13px; height: 13px; fill: var(--brand-blue-pale); flex: none; }

  .divider {
    position: absolute; left: 250px; right: 40px; top: 200px;
    height: 1.5px; background: var(--brand-blue);
  }

  .company { position: absolute; right: 40px; top: 216px; text-align: right; }
  .company__name { font-size: 17px; color: var(--brand-blue-light); margin-bottom: 8px; }
  .company__address { font-size: 15px; color: var(--text-white); line-height: 22px; }

  .footer-strip {
    position: absolute; left: 0; width: 330px; top: 322px; height: 9px;
    background: var(--strip-grey);
  }
  .footer-band {
    position: absolute; right: 0; bottom: 0; width: 380px; height: 55px;
    background: linear-gradient(90deg, var(--brand-blue) 0%, var(--brand-blue-light) 100%);
    border-top-left-radius: 40px 26px;
  }
  .footer-band__web {
    position: absolute; right: 40px; bottom: 14px;
    font-size: 17px; color: var(--text-white);
  }
</style>
</head>
<body>
  <section class="card card--back" aria-label="Card back">
    <div class="back-wordmark">Vantrell</div>
  </section>

  <section class="card card--front" aria-label="Card front">
    <div class="front-wordmark">Vantrell</div>

    <div class="person">
      <div class="person__name">Marcus Hale</div>
      <div class="person__title">Managing Director</div>
    </div>

    <ul class="contact-list">
      <li>
        <svg viewBox="0 0 24 24" aria-hidden="true"><path d="M6.6 10.8a15.1 15.1 0 0 0 6.6 6.6l2.2-2.2a1 1 0 0 1 1-.25 11.4 11.4 0 0 0 3.6.57 1 1 0 0 1 1 1V20a1 1 0 0 1-1 1A17 17 0 0 1 3 4a1 1 0 0 1 1-1h3.5a1 1 0 0 1 1 1c0 1.25.2 2.45.57 3.57a1 1 0 0 1-.25 1z"/></svg>
        555-0142-2200 (Ext. 12)
      </li>
      <li>
        <svg viewBox="0 0 24 24" aria-hidden="true"><path d="M7 1h10a2 2 0 0 1 2 2v18a2 2 0 0 1-2 2H7a2 2 0 0 1-2-2V3a2 2 0 0 1 2-2zm0 3v14h10V4zm5 15.5a1.2 1.2 0 1 0 0 2.4 1.2 1.2 0 0 0 0-2.4z"/></svg>
        555-0187-4419
      </li>
      <li>
        <svg viewBox="0 0 24 24" aria-hidden="true"><path d="M6 2h9l3 3v4H6zm-3 8h18a1 1 0 0 1 1 1v7a1 1 0 0 1-1 1h-3v3H6v-3H3a1 1 0 0 1-1-1v-7a1 1 0 0 1 1-1zm5 6v4h8v-4z"/></svg>
        555-0163-9052
      </li>
      <li>
        <svg viewBox="0 0 24 24" aria-hidden="true"><path d="M2 5h20v14H2zm2 2v.5l8 5.5 8-5.5V7zm0 3v7h16v-7l-8 5.5z"/></svg>
        mhale@vantrellforge.com
      </li>
    </ul>

    <div class="divider"></div>

    <div class="company">
      <div class="company__name">Vantrell Forge Works, Inc.</div>
      <div class="company__address">1870 Kestrel Road, Dayton Falls,<br>Ohio, US 45420</div>
    </div>

    <div class="footer-strip"></div>
    <div class="footer-band">
      <div class="footer-band__web">www.vantrellforge.com</div>
    </div>
  </section>
</body>
</html>
```